Criação de Layout para Website para Engenharia e Construção Civil
" Empresa de projetos e serviços de construção Civil que atua no seguimento de licitações publicas, obras e reformas particulares, avaliações e pericias, gerenciamento de contratos, orçamentos, planejamento. Sou Engenheiro Civil e devido à demanda no seguimento de projetos tenho três engenheiros que trabalham na empresa sob-regime de prestação de serviços, ou seja, sem vinculo direto (nesse caso parecido com o sistema Formavo e seus desainer´s). "

```html
<!DOCTYPE html>
<html lang="pt-BR">
<head>
<meta charset="utf-8">
<title>OBRAVE – Engenharia & Construção Civil</title>
<link href="https://fonts.googleapis.com/css2?family=Montserrat:wght@400;700;800&family=Open+Sans:wght@400;600;700&display=swap" rel="stylesheet">
<style>
:root{
  --green:#3cb54a;
  --green-dark:#2a8f38;
  --forest:#1d4f28;
  --ink:#3a3a3a;
  --muted:#8a8a8a;
  --gray:#f1f1f1;
  --yellow:#f4e21c;
  --white:#ffffff;
}
*{margin:0;padding:0;box-sizing:border-box}
html,body{width:1200px;height:1200px;overflow:hidden;background:var(--white)}
body{font-family:"Open Sans",Arial,sans-serif;color:var(--ink)}
.page{position:absolute;left:396px;top:0;width:408px;height:1200px;overflow:hidden;background:var(--white);box-shadow:0 0 6px rgba(0,0,0,.12)}
section,header,footer{position:absolute;left:0;width:408px}

/* header */
.hero{top:0;height:228px;background:linear-gradient(120deg,#d9c8b2 0%,#b9a58e 35%,#e3dccf 60%,#c7b08c 100%)}
.hero-photo{position:absolute;inset:0}
.nav{position:absolute;left:0;top:0;width:100%;height:26px;background:rgba(40,40,40,.72);display:flex;align-items:center;justify-content:space-between;padding:0 10px}
.brand{display:flex;align-items:center;gap:4px;font-family:"Montserrat",sans-serif;font-weight:800;font-size:10px;color:var(--white)}
.brand i{display:block;width:9px;height:9px;background:var(--green)}
.menu{display:flex;gap:6px;font-family:"Montserrat",sans-serif;font-size:4.2px;font-weight:700;color:var(--white);text-transform:uppercase}
.menu span{padding:3px 4px}
.menu .active{background:var(--green);border-radius:2px}
.hero-text{position:absolute;left:190px;top:100px;font-family:"Montserrat",sans-serif;font-weight:700;line-height:1.15}
.hero-text .l1{font-size:15px;color:var(--white);text-shadow:0 1px 2px rgba(0,0,0,.35)}
.hero-text .l2{font-size:12px;color:var(--green);text-shadow:0 1px 2px rgba(0,0,0,.25)}

/* section titles */
.title{position:absolute;left:0;width:100%;display:flex;justify-content:center;align-items:center;gap:6px}
.title h2{font-family:"Montserrat",sans-serif;font-weight:800;font-size:11px;line-height:1.05;text-align:right;color:var(--forest);text-transform:uppercase}
.title h2 b{color:var(--green);font-weight:800}
.title .rule{width:1px;height:22px;background:var(--forest)}
.title .mark{display:flex;align-items:center;gap:3px;font-family:"Montserrat",sans-serif;font-weight:800;font-size:9px;color:var(--forest)}
.title .mark i{display:block;width:8px;height:8px;background:var(--green)}

/* specialties */
.specialty{top:228px;height:168px;background:var(--white)}
.specialty .title{top:20px}
.spec-list{position:absolute;top:66px;left:18px;right:18px;display:flex;justify-content:space-between}
.spec{width:62px;text-align:center}
.spec .icon{width:26px;height:26px;border-radius:50%;background:var(--green);margin:0 auto 6px;display:flex;align-items:center;justify-content:center}
.spec h3{font-size:5.5px;font-weight:700;color:var(--green);margin-bottom:3px}
.spec p{font-size:4.2px;line-height:1.4;color:var(--muted)}

/* areas */
.areas{top:396px;height:228px;background:var(--gray)}
.areas .title{top:18px}
.arrows{position:absolute;display:flex;gap:2px}
.arrows span{width:9px;height:9px;background:#cfcfcf;display:flex;align-items:center;justify-content:center}
.areas .arrows{right:14px;top:34px}
.cards{position:absolute;top:62px;left:14px;right:14px;display:flex;justify-content:space-between}
.card{width:116px}
.card .photo{width:116px;height:86px}
.card h3{font-size:5.5px;font-weight:700;color:var(--forest);margin:6px 0 3px}
.card p{font-size:4.2px;line-height:1.4;color:var(--muted)}

/* green band */
.band{top:640px;height:86px;background:linear-gradient(90deg,var(--green-dark),var(--green))}
.band-text{position:absolute;left:52px;top:22px;font-family:"Montserrat",sans-serif;color:var(--white);font-weight:700;font-size:8.5px;line-height:1.15;text-transform:uppercase}
.band-text span{display:block;text-transform:none;font-weight:400;font-size:8px}
.btn{position:absolute;left:52px;top:56px;background:var(--yellow);color:var(--forest);font-family:"Montserrat",sans-serif;font-weight:800;font-size:4.6px;padding:4px 9px;text-transform:uppercase}
.band-photo{position:absolute;left:238px;top:10px;width:72px;height:58px;border:3px solid var(--white);transform:rotate(-6deg);background:linear-gradient(135deg,#e8efe6,#b9ccb7)}

/* portfolio */
.works{top:726px;height:226px;background:var(--white)}
.works .title{top:16px}
.works .arrows{right:14px;top:32px}
.grid{position:absolute;top:70px;left:14px;display:grid;grid-template-columns:80px 110px 80px 80px;grid-template-rows:66px 66px;gap:2px;width:380px}
.tile{position:relative}
.tile.tall{grid-row:span 2;background:linear-gradient(180deg,#8fb06a,#5f7f3e)}
.tile .caption{position:absolute;left:0;right:0;bottom:6px;text-align:center;font-size:4.5px;font-weight:700;color:var(--white);text-transform:uppercase}

/* clients */
.clients{top:952px;height:152px;background:var(--gray)}
.clients .title{top:16px}
.partners{position:absolute;left:20px;top:66px;display:grid;grid-template-columns:repeat(2,28px);gap:9px 12px}
.partners span{display:block;width:28px;height:7px;background:#d8322c;border-radius:1px}
.testimonials{position:absolute;left:140px;top:62px;display:flex;gap:10px}
.quote{width:118px;height:66px;background:var(--white);position:relative;padding:12px 8px 0}
.quote .q{position:absolute;left:50%;top:-5px;width:10px;height:10px;margin-left:-5px;background:var(--forest)}
.quote p{font-size:4.2px;line-height:1.4;color:var(--muted);text-align:center}
.quote .name{position:absolute;left:0;right:0;bottom:-9px;text-align:center;font-size:4.5px;font-weight:700;color:var(--forest)}

/* footer */
.footer{top:1104px;height:96px;background:var(--forest);color:var(--white)}
.cols{position:absolute;left:18px;top:12px;display:flex;gap:26px}
.col h4{font-family:"Montserrat",sans-serif;font-size:5px;font-weight:700;text-transform:uppercase;margin-bottom:4px;display:flex;align-items:center;gap:3px}
.col p{font-size:4.2px;line-height:1.55;opacity:.85}
.col p + h4{margin-top:5px}
.foot-brand{position:absolute;right:18px;top:30px;display:flex;align-items:center;gap:4px;font-family:"Montserrat",sans-serif;font-weight:800;font-size:10px}
.foot-brand i{display:block;width:10px;height:10px;background:var(--green)}
.up{position:absolute;right:22px;top:12px;width:10px;height:10px;border-radius:50%;border:1px solid var(--white);display:flex;align-items:center;justify-content:center}
</style>
</head>
<body>
<div class="page">

  <header class="hero">
    <div class="hero-photo" role="img" aria-label="Foto de engenheiros com capacetes analisando uma planta de obra"></div>
    <nav class="nav">
      <div class="brand"><i></i>OBRAVE</div>
      <div class="menu">
        <span class="active">Página inicial</span><span>Empresa</span><span>Áreas de atuação</span><span>Parceiros</span><span>Contato</span>
      </div>
    </nav>
    <div class="hero-text">
      <div class="l1">Prestamos serviços de</div>
      <div class="l2">Engenharia &amp; Construção Civil</div>
    </div>
  </header>

  <section class="specialty">
    <div class="title">
      <h2><b>Nossa</b><br>Especialidade</h2><span class="rule"></span><div class="mark"><i></i>OBRAVE</div>
    </div>
    <div class="spec-list">
      <div class="spec"><div class="icon"><svg width="14" height="14" viewBox="0 0 14 14"><path d="M2 11h10M3 11V6l4-3 4 3v5" fill="none" stroke="#fff" stroke-width="1.4"/></svg></div><h3>Texto aqui</h3><p>Breve descrição do serviço prestado.</p></div>
      <div class="spec"><div class="icon"><svg width="14" height="14" viewBox="0 0 14 14"><rect x="2" y="3" width="10" height="8" fill="none" stroke="#fff" stroke-width="1.4"/><path d="M4 6h6M4 8h4" stroke="#fff" stroke-width="1"/></svg></div><h3>Texto aqui</h3><p>Breve descrição do serviço prestado.</p></div>
      <div class="spec"><div class="icon"><svg width="14" height="14" viewBox="0 0 14 14"><path d="M3 7l3 3 5-6" fill="none" stroke="#fff" stroke-width="1.6"/></svg></div><h3>Texto aqui</h3><p>Breve descrição do serviço prestado.</p></div>
      <div class="spec"><div class="icon"><svg width="14" height="14" viewBox="0 0 14 14"><circle cx="7" cy="7" r="4.5" fill="none" stroke="#fff" stroke-width="1.4"/><path d="M7 4.5V7l2 1.5" stroke="#fff" stroke-width="1.2" fill="none"/></svg></div><h3>Texto aqui</h3><p>Breve descrição do serviço prestado.</p></div>
      <div class="spec"><div class="icon"><svg width="14" height="14" viewBox="0 0 14 14"><path d="M3 11V8M6 11V5M9 11V7M12 11V3" stroke="#fff" stroke-width="1.6"/></svg></div><h3>Texto aqui</h3><p>Breve descrição do serviço prestado.</p></div>
    </div>
  </section>

  <section class="areas">
    <div class="title">
      <h2><b>Áreas</b><br>de atuação</h2><span class="rule"></span><div class="mark"><i></i>OBRAVE</div>
    </div>
    <div class="arrows"><span><svg width="5" height="5" viewBox="0 0 5 5"><path d="M3.5 0.5L1.5 2.5l2 2" stroke="#fff" fill="none"/></svg></span><span><svg width="5" height="5" viewBox="0 0 5 5"><path d="M1.5 0.5l2 2-2 2" stroke="#fff" fill="none"/></svg></span></div>
    <div class="cards">
      <div class="card"><div class="photo" role="img" aria-label="Foto de engenheiros avaliando um imóvel" style="background:linear-gradient(135deg,#c9d4dc,#8ea3b3)"></div><h3>Avaliações &amp; Perícias</h3><p>Breve texto sobre esta área de atuação da empresa, com detalhes do serviço.</p></div>
      <div class="card"><div class="photo" role="img" aria-label="Foto de equipe em obra de reforma" style="background:linear-gradient(135deg,#a7b6c6,#6f7f8f)"></div><h3>Obras e Reformas</h3><p>Breve texto sobre esta área de atuação da empresa, com detalhes do serviço.</p></div>
      <div class="card"><div class="photo" role="img" aria-label="Foto de planta técnica com caneta sobre a mesa" style="background:linear-gradient(135deg,#e7eef5,#b6c7d8)"></div><h3>Licitações Públicas</h3><p>Breve texto sobre esta área de atuação da empresa, com detalhes do serviço.</p></div>
    </div>
  </section>

  <section class="band">
    <div class="band-text">Temos muitos trabalhos<span>e muita história para contar!</span></div>
    <div class="btn">Saiba mais</div>
    <div class="band-photo" role="img" aria-label="Foto de profissionais analisando projetos"></div>
  </section>

  <section class="works">
    <div class="title">
      <h2><b>O que</b><br>já fizemos</h2><span class="rule"></span><div class="mark"><i></i>OBRAVE</div>
    </div>
    <div class="arrows"><span><svg width="5" height="5" viewBox="0 0 5 5"><path d="M3.5 0.5L1.5 2.5l2 2" stroke="#fff" fill="none"/></svg></span><span><svg width="5" height="5" viewBox="0 0 5 5"><path d="M1.5 0.5l2 2-2 2" stroke="#fff" fill="none"/></svg></span></div>
    <div class="grid">
      <div class="tile" role="img" aria-label="Foto de condomínio com jardim" style="background:linear-gradient(180deg,#a9c48e,#5d7e45)"></div>
      <div class="tile tall" role="img" aria-label="Foto de área verde de projeto concluído"><div class="caption">Título do projeto</div></div>
      <div class="tile" role="img" aria-label="Foto de interior reformado" style="background:linear-gradient(180deg,#e2ddd5,#b8ad9c)"></div>
      <div class="tile" role="img" aria-label="Foto de casa residencial" style="background:linear-gradient(180deg,#c9cfd4,#7c7468)"></div>
      <div class="tile" role="img" aria-label="Foto de edifício comercial" style="background:linear-gradient(180deg,#b7c2c9,#6b747a)"></div>
      <div class="tile" role="img" aria-label="Foto de sala ampla reformada" style="background:linear-gradient(180deg,#ece8e1,#c6bcae)"></div>
      <div class="tile" role="img" aria-label="Foto de residência de dois andares" style="background:linear-gradient(180deg,#cfd6dc,#6f665c)"></div>
    </div>
  </section>

  <section class="clients">
    <div class="title">
      <h2><b>Clientes</b><br>&amp; parceiros</h2><span class="rule"></span><div class="mark"><i></i>OBRAVE</div>
    </div>
    <div class="partners"><span></span><span></span><span></span><span></span><span></span><span></span></div>
    <div class="testimonials">
      <div class="quote"><span class="q"></span><p>Depoimento curto de um cliente satisfeito com o trabalho realizado.</p><div class="name">Nome Cliente</div></div>
      <div class="quote"><span class="q"></span><p>Depoimento curto de um cliente satisfeito com o trabalho realizado.</p><div class="name">Nome Cliente</div></div>
    </div>
  </section>

  <footer class="footer">
    <div class="cols">
      <div class="col"><h4>Mapa do site</h4><p>Página Inicial<br>Nossa Empresa<br>Áreas de Atuação<br>Parceiros<br>Política de Privacidade<br>Contato</p></div>
      <div class="col"><h4><svg width="6" height="6" viewBox="0 0 6 6"><path d="M1 0.5h1.3l.5 1.4-.8.6a3.5 3.5 0 0 0 1.5 1.5l.6-.8 1.4.5V5a.6.6 0 0 1-.6.6A5 5 0 0 1 .4 1.1.6.6 0 0 1 1 .5z" fill="#fff"/></svg>Telefones</h4><p>+55 (11) 4000-1020<br>+55 (11) 95555-0188</p><h4>E-mail</h4><p>contato@obrave.com</p></div>
      <div class="col"><h4><svg width="6" height="6" viewBox="0 0 6 6"><path d="M3 .3a2 2 0 0 1 2 2C5 3.8 3 5.7 3 5.7S1 3.8 1 2.3a2 2 0 0 1 2-2z" fill="#fff"/></svg>Onde estamos</h4><p>Rua das Obras, 100<br>Centro – São Paulo, SP<br>CEP 01000-000</p></div>
    </div>
    <div class="up"><svg width="5" height="5" viewBox="0 0 5 5"><path d="M0.8 3.3L2.5 1.5l1.7 1.8" stroke="#fff" fill="none"/></svg></div>
    <div class="foot-brand"><i></i>OBRAVE</div>
  </footer>

</div>
</body>
</html>
```